Dental office stationary (letterhead, envelopes), business cards, presentation folders

Nothing too dental outside of the logo. I will need all stationary, presentation folders, business cards. Would prefer to stay in the colors of the logo

Gordon Patel, DDS
Bright Haven Dental Implant Center
555-318-2790
info@brighthavendental.example
4817 NW Maple Crest Rd Unit B
Stuart, FL 00000

Also need appointment date and time
And cancellation policy
I want it to say “kindly ask for
A 48hr cancellation policy to avoid incurring a cancellation fee”

Industry/Entity Type

Dental

Colors
0054AA
0677BA
7BADD7
CADEEF
E8F1F8

Requirements
Must have
• Name of your office, name of doctor, address, phone number
Should not have
• Too much tooth/dental. Only the tooth in logo

```html
<!DOCTYPE html>
<html lang="en">
<head>
<meta charset="utf-8">
<title>Bright Haven Dental Implant Center – Business Card</title>
<link rel="stylesheet" href="https://fonts.googleapis.com/css2?family=Roboto:ital,wght@0,400;0,500;0,700;1,400;1,500;1,700&display=swap">
<style>
  :root {
    --page-bg: #1e1f22;
    --blue-deep: #0054AA;
    --blue-mid: #0677BA;
    --blue-bright: #18b4ea;
    --blue-soft: #7BADD7;
    --blue-pale: #CADEEF;
    --blue-mist: #E8F1F8;
    --teal-rim: #17b18f;
    --white: #ffffff;
  }
  * { box-sizing: border-box; margin: 0; padding: 0; }
  html, body {
    width: 1200px; height: 900px; overflow: hidden;
    background: var(--page-bg);
    font-family: "Roboto", Arial, sans-serif;
  }
  .sheet {
    width: 1200px; height: 900px;
    display: flex; flex-direction: column;
    align-items: center; justify-content: center; gap: 60px;
  }
  .card {
    position: relative;
    width: 630px; height: 360px;
    overflow: hidden;
    background: linear-gradient(160deg, var(--blue-bright) 0%, var(--blue-mid) 45%, var(--blue-deep) 100%);
    box-shadow: 0 10px 30px rgba(0,0,0,.5);
  }
  /* Front */
  .card-front .seal {
    position: absolute; inset: 0;
    width: 630px; height: 360px;
  }
  .contact {
    position: absolute; left: 46px; top: 46px;
    color: var(--white); font-style: italic;
  }
  .contact .doctor { font-size: 21px; font-weight: 700; line-height: 1.1; }
  .contact .practice { font-size: 15px; font-weight: 400; margin-top: 3px; }
  .contact .address { font-size: 15px; line-height: 1.3; margin-top: 26px; }
  .contact .lines { list-style: none; margin-top: 26px; font-size: 15px; line-height: 1.5; }
  .contact .lines li { display: flex; align-items: center; gap: 8px; }
  .contact .lines svg { width: 14px; height: 14px; flex: none; }
  .seal-name {
    position: absolute; left: 390px; top: 168px; width: 230px;
    text-align: center;
    color: var(--blue-mid);
    font-size: 27px; font-weight: 500; letter-spacing: 1px;
    text-transform: uppercase;
  }
  /* Back */
  .card-back .emblem-area {
    position: absolute; inset: 0;
    background: radial-gradient(ellipse 45% 60% at 50% 55%, rgba(123,173,215,.35), rgba(123,173,215,0) 70%);
  }
  .back-name {
    position: absolute; inset: 0;
    display: flex; align-items: center; justify-content: center;
    color: var(--white);
    font-size: 46px; font-weight: 500; letter-spacing: 3px;
    text-transform: uppercase;
  }
</style>
</head>
<body>
<main class="sheet">
  <section class="card card-front">
    <svg class="seal" viewBox="0 0 630 360" aria-hidden="true">
      <circle cx="505" cy="235" r="228" fill="var(--teal-rim)"/>
      <circle cx="510" cy="235" r="222" fill="var(--white)"/>
      <circle cx="512" cy="235" r="200" fill="var(--blue-mist)" opacity=".55"/>
    </svg>
    <div class="contact">
      <p class="doctor">Gordon Patel, DDS</p>
      <p class="practice">Bright Haven Dental Implant Center</p>
      <p class="address">4817 NW Maple Crest Rd Unit B<br>Stuart, FL 00000</p>
      <ul class="lines">
        <li>
          <svg viewBox="0 0 24 24" fill="var(--white)"><path d="M6.6 10.8a15.1 15.1 0 0 0 6.6 6.6l2.2-2.2c.3-.3.7-.4 1-.2 1.1.4 2.3.6 3.6.6.6 0 1 .4 1 1V20c0 .6-.4 1-1 1A17 17 0 0 1 3 4c0-.6.4-1 1-1h3.5c.6 0 1 .4 1 1 0 1.3.2 2.5.6 3.6.1.3 0 .7-.2 1z"/></svg>
          <span>555-318-2790</span>
        </li>
        <li>
          <svg viewBox="0 0 24 24" fill="var(--white)"><path d="M3 5h18v14H3z" fill="none" stroke="var(--white)" stroke-width="2"/><path d="M3 6l9 7 9-7" fill="none" stroke="var(--white)" stroke-width="2"/></svg>
          <span>info@brighthavendental.example</span>
        </li>
        <li>
          <svg viewBox="0 0 24 24"><circle cx="12" cy="12" r="9" fill="none" stroke="var(--white)" stroke-width="2"/><path d="M3 12h18M12 3c3 3 3 15 0 18M12 3c-3 3-3 15 0 18" fill="none" stroke="var(--white)" stroke-width="1.6"/></svg>
          <span>www.brighthavendental.example</span>
        </li>
      </ul>
    </div>
    <p class="seal-name">Bright Haven</p>
  </section>

  <section class="card card-back">
    <div class="emblem-area" role="img" aria-label="Soft blue backdrop behind the practice name"></div>
    <p class="back-name">Bright Haven</p>
  </section>
</main>
</body>
</html>
```